Merrisol. Sunless Tanning Mousse Label

I'm looking for a label creation for a new brand of sunless tanning solutions. They are in 6.7oz bottles (template attached).

For the front of the bottle (see template) I would like an abstract multi coloured design taking up just over half the top of the bottle (approx 60%) and going around the design (this is similar to the design inspiration attached). I would this design to use the attached colour palette of pinks. It can be swirls, drips, squares, lines, whatever you think will look good.

The logo will then be over top of that abstract design in the upper 1/3, in the colour #3fe0d0

Under the abstract design the following text:

Amber Hush (Larger text)
Violet Base (2nd heading)
1 Hour Sunless Mousse (Sub text)
The No Orange Guarantee! (Sub text)
Vegan Formula (sub text)

The sub texts for above can be fun, have coloured background, different fonts, whatever looks good and is sill fun.

Towards the bottom of the front of bottle we require the sizing information:

200ml 6.7 Fl Oz

On the left side of the front (so in the template the middle smaller section) I would like the phrase "You ain't gotta get ready if you stay ready" Could you please make this as a separate little quote, with a fun design to it. It's like a little hidden gem on the side of the bottle.

On the back of the bottle for now can you please start towards the top with:

Amber Hush Mousse (larger)
Violet base (second heading)
Deep Mediterranean Inspired Tan (second heading)
Easy to Apply & Streak Free
Vegan friendly & 100% natural DHA tan actives

Under this I require approx 1.5" of Lorem Ipsum for now which will take the place of directions for using the product.

Under that in small writing can we include "Warning: This product does not contain a sunscreen and will not protect against sunburn. For external use only. If skin irritation occurs, discontinue use. Carry out a patch test 24 hours prior to full body use. Store below 25(degrees sign)C."

At the bottom is the smallest yet still legible writing, can we include the ingredients that are listed below.

Target Market(s)

Females 24-35 who take care of themselves and always want to look good. It's a youthful fun product.

Requirements
Must have
• Bright colours, and just screams FUN and youthful.

Ingredients must be listed on the back. They dont' need to take up more than an inch in height, less if possible.
*******************************************

INGREDIENTS: Water (Aqua), Propylene Glycol, Dihydroxyacetone, Peg-6 Caprylic/Capric Glycerides, Dihydroxypropyl Peg-5 Linoleammonium Chloride, Peg-7 Glyceryl Cocoate, Caramel,
Phenoxyethanol, Caprylyl Glycol, Potassium Sorbate, Hexylene Glycol, Glycerin, Helianthus Annuus (Sunflower) Seed Oil, Beta Vulgaris (Beet) Root Extract, Panthenol, Solanum Lycopersicum
(Tomato) Fruit Extract, Vaccinium Macrocarpon (Cranberry) Fruit Extract, L-ascorbic Acid (Vitamin C), Tocopheryl Acetate (Vitamin E), Theobroma Cacao (Cocoa) Seed Butter, Rosa Canina (Rose Hip)
Fruit Oil, Glycine Soja (Soybean) Oil, Cucumis Sativus (Cucumber) Fruit Extract, Blue 1 (CI 42090), Red 40 (CI 16035), Yellow 6 (CI 15985), Green 5 (CI 61570), Yellow 5 (CI 19140), Red 33 (CI 17200)

*****************************
Nice to have
• Several options to choose from, some can include a gradient into geometric shapes, rather than solid colour. Experiment
Should not have
• Do not want it to look medical.
Want colours to stay in the same pink family for the abstract design - can use white also.

```html
<!DOCTYPE html>
<html lang="en">
<head>
<meta charset="utf-8">
<title>Merrisol – Amber Hush Mousse Label</title>
<link href="https://fonts.googleapis.com/css2?family=Montserrat:wght@400;500;600;700&family=Roboto:wght@400;500&family=Yellowtail&display=swap" rel="stylesheet">
<style>
  :root{
    --canvas:#ffffff;
    --pink:#e6157f;
    --hot-pink:#ec1c8c;
    --soft-pink:#f27cc3;
    --violet:#a4188c;
    --plum:#b04aa6;
    --ink:#1d1d1d;
    --text:#222222;
    --yellow:#f6e21a;
    --teal:#3cc9b8;
    --white:#ffffff;
  }
  *{margin:0;padding:0;box-sizing:border-box}
  html,body{width:800px;height:1200px;overflow:hidden;background:var(--canvas)}
  body{position:relative;font-family:"Roboto",Arial,sans-serif;color:var(--text)}

  .label{
    position:absolute;left:20px;top:283px;width:905px;height:755px;
    transform:scale(0.84);transform-origin:top left;
    overflow:hidden;background:var(--white);
    box-shadow:0 4px 18px rgba(0,0,0,.12);
  }
  .marble{
    position:absolute;inset:0 0 250px 0;
    background:
      radial-gradient(ellipse 180px 120px at 120px 120px, var(--soft-pink), transparent 70%),
      radial-gradient(ellipse 220px 160px at 560px 260px, var(--plum), transparent 70%),
      radial-gradient(ellipse 200px 140px at 780px 330px, var(--soft-pink), transparent 70%),
      radial-gradient(ellipse 240px 180px at 320px 360px, var(--violet), transparent 70%),
      radial-gradient(ellipse 200px 150px at 820px 80px, var(--plum), transparent 70%),
      linear-gradient(135deg, var(--hot-pink), var(--pink) 45%, #d42c9c 75%, var(--hot-pink));
  }
  .wave{position:absolute;inset:0;width:905px;height:755px}

  .side-title{
    position:absolute;left:42px;top:372px;
    transform:rotate(-90deg);transform-origin:top left;
    font-family:"Montserrat",Arial,sans-serif;font-weight:600;
    color:var(--white);font-size:86px;line-height:80px;letter-spacing:1px;
    white-space:nowrap;
  }

  .quote{position:absolute;left:382px;top:378px;transform:rotate(-90deg);transform-origin:top left;white-space:nowrap}
  .quote-main{font-family:"Montserrat",Arial,sans-serif;font-weight:600;font-size:19px;color:var(--white);letter-spacing:.5px;display:block}
  .quote-script{font-family:"Yellowtail",cursive;font-size:38px;color:var(--yellow);display:block;margin:-4px 0 0 40px;line-height:44px}

  .brand{
    position:absolute;left:515px;top:95px;display:flex;align-items:center;gap:10px;
    font-family:"Montserrat",Arial,sans-serif;font-weight:500;font-size:60px;color:var(--white);letter-spacing:1px;
  }
  .brand-dot{width:14px;height:14px;border-radius:50%;background:var(--white);margin-top:28px}

  .front{position:absolute;left:515px;top:455px;font-family:"Montserrat",Arial,sans-serif}
  .front-name{font-weight:600;line-height:.95}
  .front-name .l1{display:block;font-size:58px;color:var(--ink)}
  .front-name .l2{display:block;font-size:70px;color:var(--pink);font-weight:700}
  .front-base{font-size:33px;font-weight:600;color:var(--violet);margin-top:10px;letter-spacing:1px}
  .front-sub{font-size:15px;font-weight:600;color:var(--violet);margin-top:8px}
  .front-promise{font-family:"Roboto",Arial,sans-serif;font-size:14px;color:var(--pink);margin-top:26px;letter-spacing:.3px}
  .front-vegan{display:flex;align-items:center;gap:6px;font-family:"Roboto",Arial,sans-serif;font-size:13px;color:var(--teal);margin-top:20px}

  .size-badge{
    position:absolute;left:820px;top:668px;width:56px;height:56px;border-radius:50%;
    background:linear-gradient(135deg,var(--soft-pink),var(--pink));
    color:var(--white);text-align:center;font-family:"Montserrat",Arial,sans-serif;
    display:flex;flex-direction:column;justify-content:center;
  }
  .size-badge .ml{font-size:14px;font-weight:600;line-height:14px}
  .size-badge .oz{font-size:8px;line-height:10px}

  .back{position:absolute;left:45px;top:440px;width:290px;text-align:center;font-size:10px;line-height:13px}
  .back-head{font-family:"Montserrat",Arial,sans-serif;font-weight:500;color:var(--pink);font-size:12px;line-height:15px}
  .back-head + .back-head{margin-top:6px}
  .back-claims{margin-top:7px}
  .back-directions{margin-top:9px}
  .back-warning-title{display:flex;justify-content:center;align-items:center;gap:3px;color:var(--pink);font-size:8px;font-weight:500;margin-top:14px}
  .back-warning{font-size:7px;line-height:10px;margin-top:8px}
  .back-ingredients{font-size:5px;line-height:6.4px;margin-top:8px;text-align:center}
</style>
</head>
<body>
  <section class="label">
    <div class="marble" role="img" aria-label="Abstract marbled swirl pattern in hot pink, soft pink and violet"></div>

    <svg class="wave" viewBox="0 0 905 755" aria-hidden="true">
      <path fill="#ffffff" d="M0,405 C60,392 110,380 170,384 C240,389 300,394 360,398 C420,403 440,470 482,470 C515,470 508,410 545,400 C600,386 650,400 700,406 C770,414 815,444 858,424 C880,414 892,402 905,396 L905,755 L0,755 Z"/>
      <circle cx="318" cy="412" r="18" fill="var(--pink)"/>
      <circle cx="568" cy="424" r="20" fill="var(--pink)"/>
      <circle cx="695" cy="408" r="12" fill="#ffffff"/>
      <circle cx="870" cy="432" r="12" fill="var(--pink)"/>
    </svg>

    <h2 class="side-title">AMBER<br>HUSH</h2>

    <p class="quote">
      <span class="quote-main">YOU AIN'T GOTTA GET READY</span>
      <span class="quote-script">if you stay ready</span>
    </p>

    <div class="brand"><span>Merrisol</span><span class="brand-dot"></span></div>

    <div class="front">
      <h1 class="front-name"><span class="l1">AMBER</span><span class="l2">HUSH</span></h1>
      <p class="front-base">VIOLET BASE</p>
      <p class="front-sub">1 Hour Sunless Mousse</p>
      <p class="front-promise">THE NO ORANGE GUARANTEE!</p>
      <p class="front-vegan">
        <svg width="18" height="18" viewBox="0 0 18 18" aria-hidden="true"><circle cx="9" cy="9" r="9" fill="var(--teal)"/><path d="M5 13 C6 8 9 6 13 5 C12 9 10 12 5 13 Z" fill="#fff"/></svg>
        Vegan Formula
      </p>
    </div>

    <div class="size-badge"><span class="ml">200ml</span><span class="oz">6.7 Fl Oz</span></div>

    <div class="back">
      <p class="back-head">VIOLET BASE</p>
      <p class="back-head">DEEP MEDITERRANEAN<br>INSPIRED TAN</p>
      <p class="back-claims">Easy to Apply &amp; Streak Free<br>Vegan friendly &amp; 100% natural<br>DHA tan actives</p>
      <p class="back-directions">Lorem ipsum dolor sit amet, consectetuer<br>adipiscing elit, sed diam nonummy nibh.</p>
      <p class="back-warning-title">
        <svg width="15" height="13" viewBox="0 0 15 13" aria-hidden="true"><path d="M7.5 1 L14 12 L1 12 Z" fill="none" stroke="var(--pink)" stroke-width="1.2"/><path d="M7.5 5 V8.5 M7.5 10 V10.6" stroke="var(--pink)" stroke-width="1.2"/></svg>
        WARNING
      </p>
      <p class="back-warning">This product does not contain a sunscreen and will not protect against sunburn. For external use only. If skin irritation occurs, discontinue use. Carry out a patch test 24 hours prior to full body use. Store below 25°C.</p>
      <p class="back-ingredients">INGREDIENTS: Water (Aqua), Propylene Glycol, Dihydroxyacetone, Peg-6 Caprylic/Capric Glycerides, Dihydroxypropyl Peg-5 Linoleammonium Chloride, Peg-7 Glyceryl Cocoate, Caramel, Phenoxyethanol, Caprylyl Glycol, Potassium Sorbate, Hexylene Glycol, Glycerin, Helianthus Annuus (Sunflower) Seed Oil, Beta Vulgaris (Beet) Root Extract, Panthenol, Solanum Lycopersicum (Tomato) Fruit Extract, Vaccinium Macrocarpon (Cranberry) Fruit Extract, L-ascorbic Acid (Vitamin C), Tocopheryl Acetate (Vitamin E), Theobroma Cacao (Cocoa) Seed Butter, Rosa Canina (Rose Hip) Fruit Oil, Glycine Soja (Soybean) Oil, Cucumis Sativus (Cucumber) Fruit Extract, Blue 1 (CI 42090), Red 40 (CI 16035), Yellow 6 (CI 15985), Green 5 (CI 61570), Yellow 5 (CI 19140), Red 33 (CI 17200)</p>
    </div>
  </section>
</body>
</html>
```